KAJU Freightways #ALLKAJU Business Cards & Letterhead

I am looking to business cards designed for our organization. We are currently undergoing a small re-branding that is taking place. Our organization is called KAJU Freightways and we are headquartered in Phoenix, AZ. We primarily provide transportation and logistics services to the Marlow Parcel Bureau who is our largest customer. I would like to see a design that incorporates name, title, contact info, website, and address (this will be different depending on the employee). I would also like to see some color on the business card using our logo colors or a variation. I would like our logo on the back of the business card with the website displayed. The final design should communicate that we are a next generation transportation operate that focuses on being driver-first, customer-centric, innovative, and sustainable.We would also like our #ALLKAJU catch phrase incorporated as well.

Target Market(s)

Transportation & Logistics

Industry/Entity Type

Trucking Company

Contact Information for Business Card

-First and Last Name
-Position Title
-Contact Phone
-Contact Email
-Physical Address

Font styles to use
Serif

Colors

Designer to choose colors to be used in the design.

Requirements
Must have
• -KAJU logo prominently displayed
• -#ALLKAJU catch phrase used
• -Some amount of color, design gradient, etc.
• -Logo on the back with website listed (https://www.kajufreightco.example)

```html
<!DOCTYPE html>
<html lang="en">
<head>
<meta charset="utf-8">
<title>KAJU Freightways Business Card</title>
<link rel="stylesheet" href="https://fonts.googleapis.com/css2?family=Roboto+Slab:wght@400;500;700;800&display=swap">
<style>
  :root {
    --backdrop: #b9b9b9;
    --deep-teal: #073a46;
    --leaf-green: #7cbb2b;
    --paper: #f3f3f1;
    --white: #ffffff;
    --ink: #1f2d33;
  }
  * { box-sizing: border-box; margin: 0; padding: 0; }
  html, body { width: 1200px; height: 576px; overflow: hidden; }
  body {
    background: var(--backdrop);
    font-family: "Roboto Slab", Georgia, serif;
    position: relative;
  }
  .card {
    position: absolute;
    top: 139px;
    height: 292px;
    border-radius: 10px;
    overflow: hidden;
    box-shadow: 0 3px 6px rgba(0,0,0,0.25);
  }

  /* Back of card */
  .card-back {
    left: 82px;
    width: 484px;
    background: linear-gradient(125deg, var(--leaf-green) 0%, #3f8a3d 40%, #145147 72%, var(--deep-teal) 100%);
  }
  .card-back .truck-photo {
    position: absolute;
    inset: 0;
    background: radial-gradient(ellipse at 35% 55%, rgba(255,255,255,0.12), rgba(255,255,255,0) 60%);
  }
  .back-logo {
    position: absolute;
    left: 162px;
    top: 58px;
    width: 158px;
    height: 158px;
    border: 6px solid var(--white);
    border-radius: 50%;
    display: flex;
    align-items: center;
    justify-content: center;
    color: var(--white);
    font-weight: 800;
    font-size: 42px;
  }
  .back-tagline {
    position: absolute;
    left: 0;
    right: 0;
    top: 226px;
    text-align: center;
    color: var(--leaf-green);
    font-size: 12px;
    font-weight: 700;
    letter-spacing: 2px;
  }
  .back-web {
    position: absolute;
    left: 0;
    right: 0;
    top: 261px;
    display: flex;
    align-items: center;
    justify-content: center;
    gap: 18px;
    color: var(--white);
    font-size: 12px;
    line-height: 16px;
    letter-spacing: 2.2px;
  }
  .back-web .rule {
    width: 32px;
    height: 2px;
    background: var(--leaf-green);
  }

  /* Front of card */
  .card-front {
    left: 602px;
    width: 480px;
    background: var(--paper);
  }
  .company-name {
    position: absolute;
    left: 21px;
    top: 26px;
    color: var(--deep-teal);
    font-size: 19px;
    font-weight: 700;
    line-height: 26px;
  }
  .info-band {
    position: absolute;
    left: 0;
    right: 0;
    top: 94px;
    height: 147px;
    background: var(--deep-teal);
  }
  .person-name {
    position: absolute;
    left: 21px;
    top: 110px;
    color: var(--leaf-green);
    font-size: 19px;
    font-weight: 700;
    line-height: 26px;
  }
  .person-title {
    position: absolute;
    left: 21px;
    top: 136px;
    color: var(--white);
    font-size: 13px;
    line-height: 18px;
  }
  .contact-list {
    position: absolute;
    left: 21px;
    top: 170px;
    list-style: none;
    color: var(--white);
    font-size: 12.5px;
  }
  .contact-list li {
    display: flex;
    align-items: center;
    gap: 14px;
    height: 18px;
  }
  .contact-list svg { width: 10px; height: 10px; fill: var(--leaf-green); flex: none; }
  .front-logo {
    position: absolute;
    left: 252px;
    top: 53px;
    width: 208px;
    height: 208px;
    border: 6px solid var(--leaf-green);
    border-radius: 50%;
    background: var(--paper);
    display: flex;
    align-items: center;
    justify-content: center;
    color: var(--deep-teal);
    font-weight: 800;
    font-size: 54px;
  }
  .address {
    position: absolute;
    left: 21px;
    top: 256px;
    color: var(--ink);
    font-size: 13px;
    line-height: 18px;
  }
</style>
</head>
<body>
  <section class="card card-back">
    <div class="truck-photo" role="img" aria-label="Faded photo of a freight truck cab under a green-to-teal tint"></div>
    <div class="back-logo">KAJU</div>
    <p class="back-tagline">#ALLKAJU</p>
    <div class="back-web"><span class="rule"></span><span>www.kajufreightco.example</span><span class="rule"></span></div>
  </section>

  <section class="card card-front">
    <h1 class="company-name">KAJU Freightways and<br>Energy Services</h1>
    <div class="info-band"></div>
    <p class="person-name">Dorian Keller</p>
    <p class="person-title">Chairman &amp; CEO</p>
    <ul class="contact-list">
      <li><svg viewBox="0 0 10 10"><path d="M1 3 Q5 0 9 3 L8 4.5 L6.5 3.8 L6.5 3 Q5 2.5 3.5 3 L3.5 3.8 L2 4.5 Z M2.5 5 H7.5 L8.5 9 H1.5 Z"/></svg>555-014-0236</li>
      <li><svg viewBox="0 0 10 10"><path d="M0.5 2 H9.5 V8 H0.5 Z M1 2.5 L5 5.5 L9 2.5" stroke="#073a46" stroke-width="0.8"/></svg>dorian@kajufreightco.example</li>
      <li><svg viewBox="0 0 10 10"><circle cx="5" cy="5" r="4.5"/><path d="M0.5 5 H9.5 M5 0.5 V9.5 M5 0.5 Q2 5 5 9.5 M5 0.5 Q8 5 5 9.5" stroke="#073a46" stroke-width="0.6" fill="none"/></svg>www.kajufreightco.example</li>
    </ul>
    <div class="front-logo">KAJU</div>
    <p class="address">4170 West Copper Basin Road Mesa, AZ 85201</p>
  </section>
</body>
</html>
```